Verlindo Magician

I want the business card for my business to give to people who watch that later I will be employed to show magic here is my website http://www.balsamomagicien.com/I want the interesting design , i am very opened for formal and informal, I watch a lot of design so don't stick to the common shape and form but i hope it can also be produced the thing to write on will be the same as in picture that i will upload , i also will upload the logo for you that so can be easy to useDenis CostilleMagicianMAGICIAN BALSAMO 17 rue des Tilleuls - 25000 BESANÇON contact@verlindoillusions.example tel. 0381 946 157 tel. 0674 219 503

```html
<!DOCTYPE html>
<html lang="fr">
<head>
<meta charset="utf-8">
<title>Verlindo Magician – Business Card</title>
<link rel="stylesheet" href="https://fonts.googleapis.com/css2?family=Jost:wght@300;400&display=swap">
<style>
  :root {
    --page: #e9e7e4;
    --card-dark: #1c1c1d;
    --card-light: #fbf9f9;
    --accent: #e3232b;
    --ink-light: #e8e8e8;
    --ink-dark: #111111;
    --figure-tone: #2a2a2a;
    --pattern-tint: #f4eeee;
  }
  * { margin: 0; padding: 0; box-sizing: border-box; }
  html, body {
    width: 1125px; height: 1200px; overflow: hidden;
    background: var(--page);
    font-family: "Jost", "Futura", sans-serif;
    font-weight: 300;
  }
  .canvas { position: relative; width: 1125px; height: 1200px; }
  .card {
    position: absolute; left: 150px; width: 825px; height: 472px;
  }
  .card--front { top: 98px; background: var(--card-dark); color: var(--ink-light); }
  .card--back { top: 630px; background: var(--card-light); }

  .identity { position: absolute; right: 65px; top: 66px; text-align: right; }
  .identity__name {
    color: var(--accent); font-size: 31px; font-weight: 400;
    letter-spacing: 0.5px; line-height: 1; text-transform: uppercase;
  }
  .identity__role { font-size: 21px; margin-top: 6px; line-height: 1; }
  .accent-bar {
    position: absolute; right: 0; top: 69px; width: 10px; height: 57px;
    background: var(--accent);
  }

  .contact { position: absolute; left: 62px; top: 248px; list-style: none; }
  .contact__item {
    display: flex; align-items: flex-start; font-size: 20px; line-height: 25px;
  }
  .contact__item + .contact__item { margin-top: 2px; }
  .contact__item--address { margin-bottom: 11px; }
  .contact__icon {
    width: 18px; height: 18px; margin-right: 15px; margin-top: 3px;
    fill: var(--accent); flex-shrink: 0;
  }

  .back-pattern {
    position: absolute; inset: 0;
    background: var(--pattern-tint);
    opacity: 0.55;
  }
  .portrait {
    position: absolute; left: 316px; top: 89px; width: 192px; height: 241px;
    background: linear-gradient(180deg, #3a3a3a 0%, var(--figure-tone) 60%, #111 100%);
    border-radius: 70px 70px 24px 24px;
  }
  .wordmark {
    position: absolute; left: 0; right: 0; top: 338px; text-align: center;
    font-size: 34px; font-weight: 300; color: var(--ink-dark);
    letter-spacing: 1px; text-transform: uppercase;
  }
</style>
</head>
<body>
<div class="canvas">

  <section class="card card--front">
    <div class="identity">
      <div class="identity__name">Marc Ravoulet</div>
      <div class="identity__role">Magician</div>
    </div>
    <div class="accent-bar"></div>

    <ul class="contact">
      <li class="contact__item contact__item--address">
        <svg class="contact__icon" viewBox="0 0 24 24"><path d="M12 1a8 8 0 0 0-8 8c0 6 8 14 8 14s8-8 8-14a8 8 0 0 0-8-8zm0 11a3 3 0 1 1 0-6 3 3 0 0 1 0 6z"/></svg>
        <span>MAGICIAN VERLINDO<br>17 rue des Tilleuls - 25000 BESANÇON</span>
      </li>
      <li class="contact__item">
        <svg class="contact__icon" viewBox="0 0 24 24"><path d="M6.6 10.8a15 15 0 0 0 6.6 6.6l2.2-2.2a1 1 0 0 1 1-.25 11.4 11.4 0 0 0 3.6.57 1 1 0 0 1 1 1V20a1 1 0 0 1-1 1A17 17 0 0 1 3 4a1 1 0 0 1 1-1h3.5a1 1 0 0 1 1 1c0 1.25.2 2.45.57 3.57a1 1 0 0 1-.25 1z"/></svg>
        <span>0381 946 157</span>
      </li>
      <li class="contact__item">
        <svg class="contact__icon" viewBox="0 0 24 24"><path d="M6.6 10.8a15 15 0 0 0 6.6 6.6l2.2-2.2a1 1 0 0 1 1-.25 11.4 11.4 0 0 0 3.6.57 1 1 0 0 1 1 1V20a1 1 0 0 1-1 1A17 17 0 0 1 3 4a1 1 0 0 1 1-1h3.5a1 1 0 0 1 1 1c0 1.25.2 2.45.57 3.57a1 1 0 0 1-.25 1z"/></svg>
        <span>0674 219 503</span>
      </li>
      <li class="contact__item">
        <svg class="contact__icon" viewBox="0 0 24 24"><path d="M2 6h20v12H2z" opacity="0"/><path d="M2 6l10 7 10-7v12H2z"/><path d="M2 5h20l-10 7z"/></svg>
        <span>contact@verlindoillusions.example</span>
      </li>
      <li class="contact__item">
        <svg class="contact__icon" viewBox="0 0 24 24"><circle cx="12" cy="12" r="10"/><path d="M7 8c2 0 3 1 3 3s-2 2-2 4M15 4c-1 2 0 3 2 3s2 2 1 4" stroke="#1c1c1d" stroke-width="1.6" fill="none"/></svg>
        <span>www.verlindoillusions.example</span>
      </li>
    </ul>
  </section>

  <section class="card card--back">
    <div class="back-pattern" role="img" aria-label="Faint repeating pattern of playing card suits"></div>
    <div class="portrait" role="img" aria-label="Black and white illustration of the magician in a jacket holding a playing card"></div>
    <div class="wordmark">Verlindo Magician</div>
  </section>

</div>
</body>
</html>
```